Business Card Design Project

Lorabelle is a women fashion house focusing on youthful glamour.

We bring together unique designs, premium quality materials and top craftsmanship to deliver sophisticated yet playful glamour, fun and excitement to the confident woman.

We can sum up the brand identity in 3 words:
Glamour – Sophistication – Unique

Industry/Entity Type

Fashion

Requirements
Must have
• Nim Ferrasco
nim.ferrasco@lorabelle-example.com
Mobile: 081 536 2947
Instragram: lorabelle_label
Facebook: lorabelle

Creative Director
Lorabelle Co., LTD
TEL: 02 631 48 97
42 Maple Row, 2nd Floor , D Building , Thonrak , Chaloemrat 28.
East Sanphet , Rattana , Bangkok 10240 Thailand
www.lorabelle-example.com

```html
<!DOCTYPE html>
<html lang="en">
<head>
<meta charset="utf-8">
<title>Lorabelle – Business Card</title>
<link rel="stylesheet" href="https://fonts.googleapis.com/css2?family=Roboto+Condensed:wght@300;400&display=swap">
<style>
  :root {
    --page-bg: #e9e7e4;
    --card-white: #fbfbfb;
    --card-shade: #ececec;
    --ink: #1a1a1a;
    --ink-soft: #6b6b6b;
    --rule: #cfcfcf;
    --band: #0d0d0d;
    --band-text: #f4f4f4;
  }
  * { margin: 0; padding: 0; box-sizing: border-box; }
  html, body {
    width: 1200px; height: 1000px; overflow: hidden;
    background: var(--page-bg);
    font-family: "Roboto Condensed", "Arial Narrow", sans-serif;
  }
  .card {
    position: absolute; left: 100px; top: 214px;
    width: 1000px; height: 572px;
    background: linear-gradient(90deg, var(--card-shade) 0%, var(--card-white) 45%, var(--card-white) 100%);
    box-shadow: 0 14px 40px rgba(0,0,0,.18);
    overflow: hidden;
  }
  .brand-name {
    position: absolute; left: 70px; top: 250px;
    font-weight: 300; font-size: 150px; line-height: 1;
    color: var(--ink); letter-spacing: -2px;
  }
  .divider {
    position: absolute; left: 600px; top: 40px;
    width: 1px; height: 380px; background: var(--rule);
  }
  .person { position: absolute; left: 640px; top: 52px; }
  .person-name { font-size: 27px; font-weight: 400; color: var(--ink); letter-spacing: .5px; }
  .person-title { font-size: 20px; font-weight: 300; color: var(--ink-soft); margin-top: 2px; }
  .contacts {
    position: absolute; left: 640px; top: 150px; list-style: none;
  }
  .contacts li {
    display: flex; align-items: center; height: 40px;
    font-size: 20px; font-weight: 300; color: var(--ink-soft);
  }
  .contacts svg { width: 20px; height: 20px; margin-right: 16px; flex: none; }
  .address-band {
    position: absolute; left: 0; bottom: 0; width: 100%; height: 112px;
    background: var(--band);
    display: flex; align-items: center; justify-content: flex-end;
    padding-right: 70px; gap: 22px;
  }
  .address-band svg { width: 26px; height: 34px; flex: none; }
  .address {
    font-style: normal; color: var(--band-text);
    font-size: 21px; font-weight: 400; line-height: 1.35;
  }
</style>
</head>
<body>
  <main class="card">
    <div class="brand-name">Lorabelle</div>
    <div class="divider"></div>

    <div class="person">
      <div class="person-name">NIM FERRASCO</div>
      <div class="person-title">Creative Director</div>
    </div>

    <ul class="contacts">
      <li>
        <svg viewBox="0 0 20 20"><rect x="1" y="4" width="18" height="12" fill="#1a1a1a"/><path d="M1 4 L10 11 L19 4" stroke="#fbfbfb" stroke-width="1.5" fill="none"/></svg>
        nim.ferrasco@lorabelle-example.com
      </li>
      <li>
        <svg viewBox="0 0 20 20"><rect x="5" y="1" width="10" height="18" rx="2" fill="none" stroke="#1a1a1a" stroke-width="2"/><circle cx="10" cy="15.5" r="1.2" fill="#1a1a1a"/></svg>
        081 536 2947
      </li>
      <li>
        <svg viewBox="0 0 20 20"><path d="M4 2 L8 2 L9 6 L7 8 C8 11 9 12 12 13 L14 11 L18 12 L18 16 C18 17 17 18 16 18 C8 18 2 12 2 4 C2 3 3 2 4 2 Z" fill="#1a1a1a"/></svg>
        02 631 48 97
      </li>
      <li>
        <svg viewBox="0 0 20 20"><circle cx="10" cy="10" r="8" fill="#1a1a1a"/></svg>
        lorabelle_label
      </li>
      <li>
        <svg viewBox="0 0 20 20"><circle cx="10" cy="10" r="8" fill="none" stroke="#1a1a1a" stroke-width="1.6"/><ellipse cx="10" cy="10" rx="3.5" ry="8" fill="none" stroke="#1a1a1a" stroke-width="1.4"/><line x1="2" y1="10" x2="18" y2="10" stroke="#1a1a1a" stroke-width="1.4"/></svg>
        www.lorabelle-example.com
      </li>
      <li>
        <svg viewBox="0 0 20 20"><rect x="2" y="2" width="16" height="16" fill="#1a1a1a"/></svg>
        lorabelle
      </li>
    </ul>

    <div class="address-band">
      <svg viewBox="0 0 26 34"><path d="M13 1 C6 1 1 6 1 13 C1 22 13 33 13 33 C13 33 25 22 25 13 C25 6 20 1 13 1 Z" fill="#f4f4f4"/><circle cx="13" cy="13" r="4.5" fill="#0d0d0d"/></svg>
      <address class="address">
        42 Maple Row, 2nd Floor , D Building , Thonrak , Chaloemrat 28.<br>
        East Sanphet , Rattana , Bangkok 10240 Thailand
      </address>
    </div>
  </main>
</body>
</html>
```